Harborline Renewal Business Card Design

Professional and clean design. The design colors should flow with the logo. Two-sided card with the website on the back which is:

www.HarborlineRenewal.example.

"Specializing in Water Damage Restoration"

On the front I need the name, email, phone, and logo.

Name: Darnell Quisby
Email: Darnell@HarborlineRenewal.example
Phone: 555-318-2046 for now

I only have the Preview and Thumbnail right now but should have the source files uploaded within a day or two.

Target Market(s)

Flood victims, home owners with water damage from busted pipes etc...

Industry/Entity Type

Business

Contact Information for Business Card

Name: Darnell Quisby

Font styles to use
Serif
Sans Serif

Requirements
Must have
• Business Card Details Info

```html
<!DOCTYPE html>
<html lang="en">
<head>
<meta charset="utf-8">
<title>Harborline Renewal Business Card</title>
<link rel="stylesheet" href="https://fonts.googleapis.com/css2?family=Cinzel:wght@400;600&family=Open+Sans:wght@400;600;700&display=swap">
<style>
  :root {
    --page: #ecebe8;
    --card-white: #ffffff;
    --sky: #5fc0ea;
    --ocean: #2e97d4;
    --deep: #1f7fc0;
    --pale: #a9dcf3;
    --ink-blue: #2a8fcf;
    --ink-grey: #4a4a4a;
    --serif: "Cinzel", Georgia, serif;
    --sans: "Open Sans", Arial, sans-serif;
  }
  * { margin: 0; padding: 0; box-sizing: border-box; }
  html, body { width: 1200px; height: 800px; overflow: hidden; background: var(--page); }
  .canvas { position: relative; width: 1200px; height: 800px; }
  .card {
    position: absolute; top: 245px; width: 540px; height: 309px;
    overflow: hidden; box-shadow: 0 6px 18px rgba(0,0,0,.18);
  }
  .card svg.card-art { position: absolute; inset: 0; }

  /* Back */
  .card-back { left: 40px; background: linear-gradient(160deg, var(--sky), var(--ocean)); }
  .back-brand {
    position: absolute; left: 40px; top: 88px;
    font-family: var(--serif); font-weight: 400; font-size: 34px;
    letter-spacing: 3px; color: #fff; line-height: 1.2;
  }
  .back-tagline {
    position: absolute; left: 42px; top: 186px;
    font-family: var(--sans); font-size: 13px; color: #fff; letter-spacing: .3px;
  }

  /* Front */
  .card-front { left: 620px; background: var(--card-white); }
  .front-brand {
    position: absolute; right: 28px; top: 62px;
    font-family: var(--serif); font-weight: 600; font-size: 25px;
    letter-spacing: 2px; color: var(--ink-blue); text-align: right;
  }
  .person { position: absolute; right: 28px; top: 108px; text-align: right; }
  .person-name {
    font-family: var(--serif); font-weight: 400; font-size: 19px;
    letter-spacing: 1.5px; color: var(--ink-blue);
  }
  .person-title {
    font-family: var(--sans); font-weight: 600; font-size: 10px;
    color: var(--ink-grey); letter-spacing: 1px; margin-top: 2px;
  }
  .contacts { position: absolute; right: 28px; top: 168px; list-style: none; }
  .contacts li {
    display: flex; justify-content: flex-end; align-items: center; gap: 7px;
    font-family: var(--sans); font-size: 11.5px; color: var(--ink-blue);
    line-height: 19px;
  }
  .contacts svg { width: 13px; height: 13px; }
  .address {
    position: absolute; left: 150px; top: 276px;
    font-family: var(--sans); font-weight: 700; font-size: 11px;
    color: #fff; letter-spacing: .4px;
  }
</style>
</head>
<body>
<main class="canvas">

  <section class="card card-back" aria-label="Card back">
    <svg class="card-art" width="540" height="309" viewBox="0 0 540 309" aria-hidden="true">
      <circle cx="420" cy="190" r="130" fill="#ffffff" opacity=".1"/>
    </svg>
    <h2 class="back-brand">HARBORLINE<br>RENEWAL</h2>
    <p class="back-tagline">“Specializing in Water Damage Restoration”</p>
  </section>

  <section class="card card-front" aria-label="Card front">
    <svg class="card-art" width="540" height="309" viewBox="0 0 540 309" aria-hidden="true">
      <defs>
        <linearGradient id="wave-light" x1="0" y1="0" x2="1" y2="1">
          <stop offset="0" stop-color="#7ccdf0"/>
          <stop offset="1" stop-color="#3aa3dd"/>
        </linearGradient>
        <linearGradient id="wave-deep" x1="0" y1="0" x2="1" y2="1">
          <stop offset="0" stop-color="#3aa6de"/>
          <stop offset="1" stop-color="#1f7fc0"/>
        </linearGradient>
        <linearGradient id="disc" x1="0" y1="0" x2="0" y2="1">
          <stop offset="0" stop-color="#e2f4fc"/>
          <stop offset="1" stop-color="#86d0f1"/>
        </linearGradient>
      </defs>
      <path d="M0 40 C20 170 170 195 310 215 C420 232 495 258 540 300 L540 309 L0 309 Z" fill="url(#wave-light)"/>
      <path d="M0 150 C60 215 190 228 320 240 C420 250 490 272 540 305 L540 309 L0 309 Z" fill="url(#wave-deep)"/>
      <path d="M30 170 C110 215 230 218 330 228 C430 238 495 262 540 296" fill="none" stroke="#ffffff" stroke-width="3" opacity=".85"/>
      <circle cx="100" cy="80" r="68" fill="url(#disc)" stroke="#ffffff" stroke-width="5"/>
    </svg>

    <h1 class="front-brand">HARBORLINE RENEWAL</h1>
    <div class="person">
      <p class="person-name">DARNELL QUISBY</p>
      <p class="person-title">REALTOR</p>
    </div>
    <ul class="contacts">
      <li>555-318-2046
        <svg viewBox="0 0 14 14" aria-hidden="true"><circle cx="7" cy="7" r="7" fill="#2a8fcf"/><path d="M4.5 3.5 L6 5.5 L5.2 6.4 Q6.2 8.2 7.8 8.9 L8.6 8 L10.5 9.5 L9.8 10.6 Q6.5 10.6 3.6 5 Z" fill="#fff"/></svg>
      </li>
      <li>Darnell@HarborlineRenewal.example
        <svg viewBox="0 0 14 14" aria-hidden="true"><circle cx="7" cy="7" r="7" fill="#2a8fcf"/><rect x="3.5" y="4.5" width="7" height="5" fill="#fff"/><path d="M3.5 4.5 L7 7.5 L10.5 4.5" fill="none" stroke="#2a8fcf" stroke-width=".8"/></svg>
      </li>
      <li>www.HarborlineRenewal.example
        <svg viewBox="0 0 14 14" aria-hidden="true"><circle cx="7" cy="7" r="7" fill="#2a8fcf"/><g fill="none" stroke="#fff" stroke-width=".8"><circle cx="7" cy="7" r="4"/><ellipse cx="7" cy="7" rx="1.8" ry="4"/><path d="M3 7 H11"/></g></svg>
      </li>
    </ul>
    <p class="address">P.O. BOX: 4471 POSTAL CODE: 208, PORT AVERILL.</p>
  </section>

</main>
</body>
</html>
```